Help me make landing pages for my web application that are mobile friendly

I need to make 2 mobile friendly landing pages for an application. The 2 pages will be related. First I need a home page and then I need a working page. I do not want to change the color scheme or logos. Just layout and design.

```html
<!DOCTYPE html>
<html lang="en">
<head>
<meta charset="utf-8">
<title>RelayCover – Mobile Screens</title>
<link href="https://fonts.googleapis.com/css2?family=Lato:wght@400;700&display=swap" rel="stylesheet">
<style>
:root{
  --bg:#f3f1f3;
  --teal:#35b4d6;
  --blue:#4a86c6;
  --purple:#6f4aa6;
  --label:#6a3fa3;
  --name:#2b9fd2;
  --ink:#2e2e36;
  --muted:#4a4a55;
  --card-a:#d5eaf4;
  --card-b:#e2dbef;
  --ok:#2bb0d9;
  --active:#2fbf4c;
  --cancel:#e6263f;
  --white:#ffffff;
}
*{box-sizing:border-box;margin:0;padding:0}
html,body{width:883px;height:1200px;overflow:hidden;background:var(--bg);font-family:'Lato',sans-serif;color:var(--ink)}
.canvas{position:relative;width:883px;height:1200px}
.screen{position:absolute;background:var(--white);overflow:hidden}
.hero{position:absolute;left:0;top:0;width:100%;background:linear-gradient(160deg,var(--teal) 0%,var(--blue) 45%,var(--purple) 100%)}
.wave{position:absolute;left:0;width:100%;display:block}
.status{position:absolute;top:10px;left:10px;right:10px;display:flex;justify-content:space-between;color:var(--white);font-size:7px;font-weight:700}
.status svg{height:6px}
.kebab{position:absolute;left:9px;top:34px;width:2px}
.kebab i{display:block;width:2px;height:2px;border-radius:50%;background:var(--white);margin-bottom:2px}
.brand{position:absolute;left:0;right:0;top:22px;display:flex;justify-content:center;align-items:center;gap:5px;color:var(--white);font-size:19px;font-weight:700;letter-spacing:.2px}
.brand .dot{width:9px;height:9px;border-radius:50%;background:currentColor}
.hero-title{position:absolute;left:0;right:0;top:66px;text-align:center;color:var(--white);font-size:10.5px;font-weight:700}

.info{position:absolute;left:10px;right:8px;z-index:2}
.row{display:flex;gap:8px;align-items:flex-start;position:absolute;left:0;right:0}
.ico{flex:none;width:22px;height:22px;border-radius:50%;background:var(--white);box-shadow:0 1px 4px rgba(60,60,110,.18);display:flex;align-items:center;justify-content:center}
.ico svg{width:12px;height:12px}
.row .lbl{color:var(--label);font-size:8.5px;font-weight:700;line-height:1.2}
.row .val{color:var(--muted);font-size:8px;line-height:1.2}
.row .val b{color:var(--name);font-weight:700}

.soft{position:absolute;border-radius:5px;background:linear-gradient(135deg,var(--card-a),var(--card-b))}
.soft h4{font-size:8px;font-weight:700;color:var(--ink)}
.field{background:var(--white);border-radius:4px;font-size:7.5px;color:var(--muted);display:flex;align-items:center;justify-content:space-between;padding:0 8px}
.pill{display:inline-flex;align-items:center;gap:2px;border-radius:8px;color:var(--white);font-size:5.5px;padding:1px 7px;line-height:1.4}
.pill.teal{background:var(--ok)}
.pill.violet{background:var(--purple)}
.pill.green{background:var(--active)}
.pill.red{background:var(--cancel)}
.box{width:8px;height:8px;border-radius:2px;background:#e4e4ea;display:inline-block;margin-right:6px;vertical-align:middle}

.tabs{position:absolute;left:10px;display:flex;gap:8px;align-items:center;white-space:nowrap;color:var(--white);z-index:2}
.tab{display:flex;align-items:center;gap:4px}
.tab.on{background:var(--white);color:var(--ink);border-radius:10px;padding:3px 8px}
.tab svg{width:8px;height:8px}

.list-title{position:absolute;left:12px;right:14px;display:flex;justify-content:space-between;align-items:center;font-weight:700;color:var(--ink);z-index:2}
.help{width:9px;height:9px;border-radius:50%;background:var(--blue);color:var(--white);font-size:6px;display:flex;align-items:center;justify-content:center}
.cards{position:absolute;left:14px;right:13px}
.card{position:relative;border-radius:4px;background:linear-gradient(135deg,var(--card-a),var(--card-b));padding:.8em;margin-bottom:.95em}
.card .sf{font-weight:700;color:var(--ink);font-size:1.05em}
.card .who{display:flex;align-items:center;gap:.7em;margin-top:.9em}
.avatar{width:2.4em;height:2.4em;border-radius:50%;flex:none;display:flex;align-items:center;justify-content:center;font-weight:700;color:var(--name);background:var(--white);font-size:1em}
.avatar.photo{background:linear-gradient(135deg,#c9a48c,#5a4a48)}
.who .nm{color:var(--name);font-weight:700;font-size:1.05em;line-height:1.2}
.who .rl{color:var(--muted);font-size:.95em}
.card .meta{position:absolute;left:59%;top:.7em;font-size:.82em;line-height:1.25}
.meta .k{color:var(--label);font-weight:700}
.meta p{margin-bottom:.55em}
.meta .pill{font-size:1em;padding:0 1em;margin-left:.5em}
.edit{width:.9em;height:.9em;display:block;margin-bottom:.4em}

.indicator{position:absolute;left:50%;width:72px;height:3px;margin-left:-36px;border-radius:2px;background:linear-gradient(90deg,var(--teal),var(--purple))}

.menu-brand{position:absolute;left:0;right:0;top:26px;display:flex;justify-content:center;align-items:center;gap:5px;color:var(--purple);font-size:20px;font-weight:700}
.menu-brand .dot{width:10px;height:10px;border-radius:50%;background:var(--purple)}
.nav{position:absolute;left:19px;right:18px;top:74px}
.nav a{display:flex;align-items:center;gap:10px;height:34px;padding-left:16px;color:var(--ink);font-size:11.5px;text-decoration:none;margin-bottom:0}
.nav a.on{background:linear-gradient(90deg,var(--blue),var(--purple));color:var(--white);border-radius:17px}
.nav svg{width:14px;height:14px}
.profile{position:absolute;left:0;right:0;top:229px;text-align:center;color:var(--white)}
.pic{width:52px;height:52px;border-radius:50%;background:linear-gradient(180deg,#ffffff 0%,#e9e9ee 55%,#3a3a40 56%,#2a2a30 100%);margin:0 auto}
.btn-line{display:flex;align-items:center;justify-content:center;gap:5px;width:128px;height:25px;margin:0 auto;border:1.5px solid var(--white);border-radius:13px;font-size:11px}
.btn-fill{display:flex;align-items:center;justify-content:center;gap:5px;width:128px;height:25px;margin:0 auto;border-radius:13px;background:#27b1d6;font-size:11px}
</style>
</head>
<body>
<div class="canvas">

<!-- ===== Opening information (compact) ===== -->
<section class="screen" style="left:78px;top:53px;width:189px;height:407px;border-radius:18px 18px 0 0">
  <div class="hero" style="height:112px">
    <svg class="wave" style="top:70px;height:44px" viewBox="0 0 100 40" preserveAspectRatio="none"><path d="M0 0 C0 20 10 25 30 25 H72 C92 25 100 30 100 40 H0Z" fill="#fff"/></svg>
  </div>
  <div class="status"><span>9:45</span><svg viewBox="0 0 30 6"><rect x="0" y="4" width="1.5" height="2" fill="#fff"/><rect x="2.5" y="3" width="1.5" height="3" fill="#fff"/><rect x="5" y="1.5" width="1.5" height="4.5" fill="#fff"/><path d="M11 5 l3-3 l3 3z" fill="#fff"/><rect x="21" y="1" width="8" height="4" rx="1" fill="#fff"/></svg></div>
  <div class="kebab"><i></i><i></i><i></i></div>
  <div class="brand" style="font-size:17px"><span class="dot"></span>RelayCover</div>
  <div class="hero-title">Opening Information</div>
  <div class="info" style="top:118px">
    <div class="row" style="top:0"><span class="ico"><svg viewBox="0 0 12 12"><rect x="2" y="1" width="7" height="10" rx="1" fill="#4a86c6"/><rect x="3.5" y="3" width="4" height="1" fill="#fff"/><rect x="3.5" y="5" width="4" height="1" fill="#fff"/></svg></span><div><div class="lbl">Summary</div><div class="val">Testing-test</div></div></div>
    <div class="row" style="top:31px"><span class="ico"><svg viewBox="0 0 12 12"><path d="M6 1a3.5 3.5 0 0 1 3.5 3.5C9.5 7 6 11 6 11S2.5 7 2.5 4.5A3.5 3.5 0 0 1 6 1z" fill="#4a86c6"/><circle cx="6" cy="4.5" r="1.3" fill="#fff"/></svg></span><div><div class="lbl">Location</div><div class="val">Pine Hollow Elementary School</div></div></div>
    <div class="row" style="top:63px"><span class="ico"><svg viewBox="0 0 12 12"><circle cx="7" cy="5" r="3" fill="none" stroke="#4a86c6" stroke-width="1.4"/><path d="M5 7 L2 10" stroke="#4a86c6" stroke-width="1.6"/></svg></span><div><div class="lbl">Type</div><div class="val">Vacancy</div></div></div>
    <div class="row" style="top:94px"><span class="ico"><svg viewBox="0 0 12 12"><circle cx="4" cy="4" r="1.6" fill="#4a86c6"/><circle cx="8" cy="4" r="1.6" fill="#6f4aa6"/><rect x="2" y="6.5" width="4" height="4" rx="1.5" fill="#4a86c6"/><rect x="6" y="6.5" width="4" height="4" rx="1.5" fill="#6f4aa6"/></svg></span><div><div class="lbl">Regular Staff</div><div class="val"><b>OH</b> Owen Hartley</div></div></div>
    <div class="row" style="top:126px"><span class="ico"><svg viewBox="0 0 12 12"><rect x="1.5" y="1.5" width="4" height="4" rx="1.5" fill="#4a86c6"/><rect x="6.5" y="1.5" width="4" height="4" rx="1.5" fill="#4a86c6"/><rect x="1.5" y="6.5" width="4" height="4" rx="1.5" fill="#4a86c6"/><rect x="6.5" y="6.5" width="4" height="4" rx="1.5" fill="#6f4aa6"/></svg></span><div><div class="lbl">Assignment Category</div><div class="val">Teacher</div></div></div>
    <div class="row" style="top:158px"><span class="ico"><svg viewBox="0 0 12 12"><rect x="4.5" y="1" width="3" height="3" fill="#6f4aa6"/><path d="M6 4v2M2.5 6h7M2.5 6v2M9.5 6v2" stroke="#4a86c6"/><rect x="1" y="8" width="3" height="3" fill="#4a86c6"/><rect x="8" y="8" width="3" height="3" fill="#4a86c6"/></svg></span><div><div class="lbl">Department</div><div class="val">-</div></div></div>
    <div class="row" style="top:190px"><span class="ico"><svg viewBox="0 0 12 12"><circle cx="6" cy="6" r="4.8" fill="#4a86c6"/><rect x="5.4" y="5" width="1.3" height="4" fill="#fff"/><circle cx="6" cy="3.5" r=".8" fill="#fff"/></svg></span><div><div class="lbl">Description</div><div class="val">asdf<br>sffsd</div></div></div>
  </div>
  <div class="soft" style="left:10px;right:10px;top:353px;height:70px;padding:8px 12px">
    <h4 style="font-size:7px">Comments</h4>
    <div class="field" style="position:absolute;left:10px;top:20px;width:100px;height:30px;font-size:6px;align-items:flex-start;padding-top:5px;line-height:1.4">Write a comment or upload a file....</div>
    <div style="position:absolute;right:12px;top:23px;display:flex;flex-direction:column;gap:4px;align-items:flex-end"><span class="pill teal" style="font-size:5px">Post ▸</span><span class="pill violet" style="font-size:5px">Upload ▪</span></div>
  </div>
</section>

<!-- ===== My assignments (compact) ===== -->
<section class="screen" style="left:347px;top:53px;width:189px;height:407px;border-radius:18px 18px 0 0">
  <div class="hero" style="height:122px">
    <svg class="wave" style="top:78px;height:45px" viewBox="0 0 100 40" preserveAspectRatio="none"><path d="M0 0 C0 20 10 25 30 25 H72 C92 25 100 30 100 40 H0Z" fill="#fff"/></svg>
  </div>
  <div class="status"><span>9:45</span><svg viewBox="0 0 30 6"><rect x="0" y="4" width="1.5" height="2" fill="#fff"/><rect x="2.5" y="3" width="1.5" height="3" fill="#fff"/><rect x="5" y="1.5" width="1.5" height="4.5" fill="#fff"/><path d="M11 5 l3-3 l3 3z" fill="#fff"/><rect x="21" y="1" width="8" height="4" rx="1" fill="#fff"/></svg></div>
  <div class="kebab"><i></i><i></i><i></i></div>
  <div class="brand" style="font-size:17px"><span class="dot"></span>RelayCover</div>
  <div class="tabs" style="top:66px;font-size:6px">
    <span class="tab on"><svg viewBox="0 0 8 8"><rect x="1" y="0.5" width="6" height="7" rx="1" fill="#4a86c6"/></svg>My Assignments</span>
    <span class="tab"><svg viewBox="0 0 8 8"><circle cx="4" cy="4" r="3.3" fill="none" stroke="#fff"/><path d="M4 2v2h1.5" stroke="#fff" fill="none"/></svg>Available Openings</span>
    <span class="tab"><svg viewBox="0 0 8 8"><rect x=".5" y="2" width="7" height="5" rx="1" fill="#fff"/></svg>My</span>
  </div>
  <div class="list-title" style="top:120px;font-size:9.5px"><span>My Assignments</span><span class="help">?</span></div>
  <div class="cards" style="top:145px;left:11px;right:9px;font-size:6.4px">
    <div class="card" style="height:65px;margin-bottom:7px"><div class="sf">Subbing For:</div><div class="who"><span class="avatar photo" role="img" aria-label="Portrait photo of teacher"></span><div><div class="nm">Clara Whitfield</div><div class="rl">Teacher</div></div></div><div class="meta"><svg class="edit" viewBox="0 0 8 8"><path d="M1 7 L2 5 L6 1 L7 2 L3 6Z" fill="#4a86c6"/></svg><p><span class="k">Location:</span> PHES</p><p><span class="k">Status:</span><span class="pill teal">Complete</span></p><p><span class="k">Time Slots:</span><br>09/02-09/02 (1h 0m).</p></div></div>
    <div class="card" style="height:65px;margin-bottom:7px"><div class="sf">Subbing For:</div><div class="who"><span class="avatar">T</span><div><div class="nm">Extra duty</div><div class="rl">Teacher</div></div></div><div class="meta"><svg class="edit" viewBox="0 0 8 8"><path d="M1 7 L2 5 L6 1 L7 2 L3 6Z" fill="#4a86c6"/></svg><p><span class="k">Location:</span> PHES</p><p><span class="k">Status:</span><span class="pill teal">Complete</span></p><p><span class="k">Time Slots:</span><br>07/1007/11 (1h 20m)</p></div></div>
    <div class="card" style="height:65px;margin-bottom:7px"><div class="sf">Subbing For:</div><div class="who"><span class="avatar">OH</span><div><div class="nm">Owen Hartley</div><div class="rl">Teacher</div></div></div><div class="meta"><svg class="edit" viewBox="0 0 8 8"><path d="M1 7 L2 5 L6 1 L7 2 L3 6Z" fill="#4a86c6"/></svg><p><span class="k">Location:</span> PHES</p><p><span class="k">Status:</span><span class="pill teal">Complete</span></p><p><span class="k">Time Slots:</span><br>07/1007/11 (1h 20m)</p></div></div>
    <div class="card" style="height:65px"><div class="sf">Subbing For:</div><div class="who"><span class="avatar photo" role="img" aria-label="Portrait photo of administrator"></span><div><div class="nm">Reid Calloway</div><div class="rl">Administrator</div></div></div><div class="meta"><svg class="edit" viewBox="0 0 8 8"><path d="M1 7 L2 5 L6 1 L7 2 L3 6Z" fill="#4a86c6"/></svg><p><span class="k">Location:</span> PHES</p><p><span class="k">Status:</span><span class="pill green">Active</span></p><p><span class="k">Time Slots:</span></p></div></div>
  </div>
</section>

<!-- ===== Opening information (full) ===== -->
<section class="screen" style="left:614px;top:50px;width:213px;height:993px">
  <div class="hero" style="height:122px">
    <svg class="wave" style="top:76px;height:48px" viewBox="0 0 100 40" preserveAspectRatio="none"><path d="M0 0 C0 20 10 25 30 25 H72 C92 25 100 30 100 40 H0Z" fill="#fff"/></svg>
  </div>
  <div class="status"><span>9:45</span><svg viewBox="0 0 30 6"><rect x="0" y="4" width="1.5" height="2" fill="#fff"/><rect x="2.5" y="3" width="1.5" height="3" fill="#fff"/><rect x="5" y="1.5" width="1.5" height="4.5" fill="#fff"/><path d="M11 5 l3-3 l3 3z" fill="#fff"/><rect x="21" y="1" width="8" height="4" rx="1" fill="#fff"/></svg></div>
  <div class="kebab" style="top:36px"><i></i><i></i><i></i></div>
  <div class="brand" style="top:24px"><span class="dot"></span>RelayCover</div>
  <div class="hero-title" style="top:72px;font-size:11px">Opening Information</div>
  <div class="info" style="top:128px;left:14px">
    <div class="row" style="top:0"><span class="ico" style="width:24px;height:24px"><svg viewBox="0 0 12 12"><rect x="2" y="1" width="7" height="10" rx="1" fill="#4a86c6"/><rect x="3.5" y="3" width="4" height="1" fill="#fff"/><rect x="3.5" y="5" width="4" height="1" fill="#fff"/></svg></span><div><div class="lbl" style="font-size:9.5px">Summary</div><div class="val" style="font-size:9px">Testing-test</div></div></div>
    <div class="row" style="top:35px"><span class="ico" style="width:24px;height:24px"><svg viewBox="0 0 12 12"><path d="M6 1a3.5 3.5 0 0 1 3.5 3.5C9.5 7 6 11 6 11S2.5 7 2.5 4.5A3.5 3.5 0 0 1 6 1z" fill="#4a86c6"/><circle cx="6" cy="4.5" r="1.3" fill="#fff"/></svg></span><div><div class="lbl" style="font-size:9.5px">Location</div><div class="val" style="font-size:9px">Pine Hollow Elementary School</div></div></div>
    <div class="row" style="top:71px"><span class="ico" style="width:24px;height:24px"><svg viewBox="0 0 12 12"><circle cx="7" cy="5" r="3" fill="none" stroke="#4a86c6" stroke-width="1.4"/><path d="M5 7 L2 10" stroke="#4a86c6" stroke-width="1.6"/></svg></span><div><div class="lbl" style="font-size:9.5px">Type</div><div class="val" style="font-size:9px">Vacancy</div></div></div>
    <div class="row" style="top:107px"><span class="ico" style="width:24px;height:24px"><svg viewBox="0 0 12 12"><circle cx="4" cy="4" r="1.6" fill="#4a86c6"/><circle cx="8" cy="4" r="1.6" fill="#6f4aa6"/><rect x="2" y="6.5" width="4" height="4" rx="1.5" fill="#4a86c6"/><rect x="6" y="6.5" width="4" height="4" rx="1.5" fill="#6f4aa6"/></svg></span><div><div class="lbl" style="font-size:9.5px">Regular Staff</div><div class="val" style="font-size:9px"><b>OH</b> Owen Hartley</div></div></div>
    <div class="row" style="top:143px"><span class="ico" style="width:24px;height:24px"><svg viewBox="0 0 12 12"><rect x="1.5" y="1.5" width="4" height="4" rx="1.5" fill="#4a86c6"/><rect x="6.5" y="1.5" width="4" height="4" rx="1.5" fill="#4a86c6"/><rect x="1.5" y="6.5" width="4" height="4" rx="1.5" fill="#4a86c6"/><rect x="6.5" y="6.5" width="4" height="4" rx="1.5" fill="#6f4aa6"/></svg></span><div><div class="lbl" style="font-size:9.5px">Assignment Category</div><div class="val" style="font-size:9px">Teacher</div></div></div>
    <div class="row" style="top:178px"><span class="ico" style="width:24px;height:24px"><svg viewBox="0 0 12 12"><rect x="4.5" y="1" width="3" height="3" fill="#6f4aa6"/><path d="M6 4v2M2.5 6h7M2.5 6v2M9.5 6v2" stroke="#4a86c6"/><rect x="1" y="8" width="3" height="3" fill="#4a86c6"/><rect x="8" y="8" width="3" height="3" fill="#4a86c6"/></svg></span><div><div class="lbl" style="font-size:9.5px">Department</div><div class="val" style="font-size:9px">-</div></div></div>
    <div class="row" style="top:212px"><span class="ico" style="width:24px;height:24px"><svg viewBox="0 0 12 12"><circle cx="6" cy="6" r="4.8" fill="#4a86c6"/><rect x="5.4" y="5" width="1.3" height="4" fill="#fff"/><circle cx="6" cy="3.5" r=".8" fill="#fff"/></svg></span><div><div class="lbl" style="font-size:9.5px">Description</div><div class="val" style="font-size:9px">asdf<br>sffsd</div></div></div>
  </div>

  <div class="soft" style="left:13px;right:13px;top:388px;height:94px;padding:8px 13px">
    <h4>Comments</h4>
    <div class="field" style="position:absolute;left:11px;top:22px;width:110px;height:34px;font-size:6.5px;align-items:flex-start;padding-top:6px;line-height:1.5">Write a comment or upload a file....</div>
    <div style="position:absolute;right:13px;top:26px;display:flex;flex-direction:column;gap:5px;align-items:flex-end"><span class="pill teal">Post ▸</span><span class="pill violet">Upload ▪</span></div>
    <div class="field" style="position:absolute;left:11px;right:11px;top:62px;height:22px;justify-content:center;color:var(--label);font-weight:700;font-size:7.5px">No comments or files uploaded</div>
  </div>

  <div class="soft" style="left:13px;right:13px;top:492px;height:69px;padding:8px 13px">
    <h4>Additional Details</h4>
    <div style="font-size:7px;color:var(--muted);margin:5px 0 0 -1px">Parking Spot</div>
    <div class="field" style="position:absolute;left:11px;right:11px;top:36px;height:22px"></div>
  </div>

  <div class="soft" style="left:13px;right:13px;top:571px;height:96px;padding:8px 13px">
    <h4>Time Slots</h4>
    <div style="margin-top:7px;display:flex;gap:4px"><span class="pill teal">Accept ✓</span><span class="pill violet">Withdraw ▪</span></div>
    <div class="field" style="position:absolute;left:11px;right:11px;top:41px;height:22px;justify-content:flex-start"><span class="box"></span>Date</div>
    <div class="field" style="position:absolute;left:11px;right:11px;top:67px;height:22px"><span><span class="box"></span>3/19/2026</span><svg width="12" height="11" viewBox="0 0 12 11"><rect x="0" y="1" width="12" height="10" rx="1.5" fill="#4a86c6"/><rect x="2" y="4" width="2" height="2" fill="#fff"/><rect x="5" y="4" width="2" height="2" fill="#fff"/><rect x="8" y="4" width="2" height="2" fill="#fff"/><rect x="2" y="7" width="2" height="2" fill="#fff"/><rect x="5" y="7" width="2" height="2" fill="#fff"/></svg></div>
  </div>

  <div class="soft" style="left:13px;right:13px;top:675px;height:96px;padding:8px 13px">
    <h4>From :</h4>
    <div class="field" style="position:absolute;left:11px;right:11px;top:21px;height:22px">9:30 AM<svg width="12" height="12" viewBox="0 0 12 12"><circle cx="6" cy="6" r="5" fill="none" stroke="#4a86c6" stroke-width="1.3"/><path d="M6 3v3h2" stroke="#4a86c6" fill="none"/></svg></div>
    <h4 style="position:absolute;top:49px">To :</h4>
    <div class="field" style="position:absolute;left:11px;right:11px;top:62px;height:22px">12:30 PM<svg width="12" height="12" viewBox="0 0 12 12"><circle cx="6" cy="6" r="5" fill="none" stroke="#4a86c6" stroke-width="1.3"/><path d="M6 3v3h2" stroke="#4a86c6" fill="none"/></svg></div>
  </div>

  <div class="soft" style="left:13px;right:13px;top:782px;height:81px;padding:8px 11px;font-size:7px">
    <div><span style="color:var(--label);font-weight:700">Current Assignment</span> : No Assignment</div>
    <div style="margin-top:7px"><span style="color:var(--label);font-weight:700">Status:</span> <span class="pill green" style="padding:1px 10px;margin-left:4px">Active</span></div>
    <div class="field" style="position:absolute;left:11px;right:11px;top:50px;height:22px"><span><span class="box"></span>3/19/2026</span><svg width="12" height="11" viewBox="0 0 12 11"><rect x="0" y="1" width="12" height="10" rx="1.5" fill="#4a86c6"/><rect x="2" y="4" width="2" height="2" fill="#fff"/><rect x="5" y="4" width="2" height="2" fill="#fff"/><rect x="8" y="4" width="2" height="2" fill="#fff"/><rect x="2" y="7" width="2" height="2" fill="#fff"/><rect x="5" y="7" width="2" height="2" fill="#fff"/></svg></div>
  </div>

  <div style="position:absolute;left:0;right:0;top:872px;height:73px;overflow:hidden">
    <div class="soft" style="left:13px;right:13px;top:0;height:96px;padding:8px 13px">
      <h4>From :</h4>
      <div class="field" style="position:absolute;left:11px;right:11px;top:21px;height:22px">2:30 AM<svg width="12" height="12" viewBox="0 0 12 12"><circle cx="6" cy="6" r="5" fill="none" stroke="#4a86c6" stroke-width="1.3"/><path d="M6 3v3h2" stroke="#4a86c6" fill="none"/></svg></div>
      <h4 style="position:absolute;top:49px">To :</h4>
      <div class="field" style="position:absolute;left:11px;right:11px;top:62px;height:22px">4:00 PM<svg width="12" height="12" viewBox="0 0 12 12"><circle cx="6" cy="6" r="5" fill="none" stroke="#4a86c6" stroke-width="1.3"/><path d="M6 3v3h2" stroke="#4a86c6" fill="none"/></svg></div>
    </div>
  </div>
  <div style="position:absolute;right:13px;top:956px;display:flex;gap:3px"><span class="pill teal" style="padding:1px 9px">Save ▪</span><span class="pill violet" style="padding:1px 9px">Close ✕</span></div>
  <div class="indicator" style="top:982px"></div>
</section>

<!-- ===== Menu ===== -->
<section class="screen" style="left:57px;top:516px;width:212px;height:461px">
  <div class="menu-brand"><span class="dot"></span>RelayCover</div>
  <nav class="nav">
    <a class="on" href="#"><svg viewBox="0 0 14 14"><path d="M7 1 L13 7 H11 V13 H8.5 V9 H5.5 V13 H3 V7 H1Z" fill="#fff"/></svg>Home</a>
    <a href="#" style="margin-top:5px"><svg viewBox="0 0 14 14"><circle cx="7" cy="7" r="6" fill="none" stroke="#4a86c6" stroke-width="1.5"/><path d="M7 3.5V7h2.5" stroke="#4a86c6" stroke-width="1.3" fill="none"/></svg>Available Openings</a>
    <a href="#"><svg viewBox="0 0 14 14"><rect x="2.5" y="1.5" width="9" height="11.5" rx="1.2" fill="#4a86c6"/><rect x="4.5" y="5" width="5" height="1" fill="#fff"/><rect x="4.5" y="7.5" width="5" height="1" fill="#fff"/><rect x="4.5" y="10" width="3" height="1" fill="#fff"/></svg>Assignments</a>
    <a href="#"><svg viewBox="0 0 14 14"><circle cx="8" cy="3" r="2" fill="#6f4aa6"/><path d="M1 9 H5 L8 10 H12 L10 13 H3 L1 12Z" fill="#4a86c6"/></svg>Support</a>
  </nav>
  <div class="hero" style="top:210px;height:251px;background:linear-gradient(170deg,var(--teal) 0%,var(--blue) 45%,var(--purple) 100%)">
    <svg class="wave" style="top:-1px;height:40px" viewBox="0 0 100 40" preserveAspectRatio="none"><path d="M0 0 H100 V0 C100 15 92 20 72 20 H28 C10 20 0 28 0 40Z" fill="#fff"/></svg>
  </div>
  <div class="profile">
    <div class="pic" role="img" aria-label="Default profile placeholder"></div>
    <div style="font-size:11.5px;margin:12px 0 9px">No Profile Image</div>
    <div class="btn-line"><svg width="9" height="11" viewBox="0 0 9 11"><path d="M3 0.5h1.5v5h1V3.5h1.5V6h0.5V5h1.2v4L7 11H3.5L1 7l1-0.5 1 1.2z" fill="#fff"/></svg>Click Here</div>
    <div style="font-size:11px;margin-top:7px;line-height:1.4">Greta<br>sub.two@relaycover.test</div>
    <div style="height:1px;background:rgba(255,255,255,.2);margin:12px 0 14px"></div>
    <div class="btn-fill"><svg width="10" height="10" viewBox="0 0 10 10"><rect x="1" y="0.5" width="5" height="9" rx=".8" fill="#fff"/><path d="M6 5h3.5M8 3.5L9.5 5 8 6.5" stroke="#fff" fill="none"/></svg>Log Out</div>
  </div>
</section>

<!-- ===== My assignments (full) ===== -->
<section class="screen" style="left:335px;top:516px;width:213px;height:633px">
  <div class="hero" style="height:136px">
    <svg class="wave" style="top:86px;height:51px" viewBox="0 0 100 40" preserveAspectRatio="none"><path d="M0 0 C0 20 10 25 30 25 H72 C92 25 100 30 100 40 H0Z" fill="#fff"/></svg>
  </div>
  <div class="status"><span>9:45</span><svg viewBox="0 0 30 6"><rect x="0" y="4" width="1.5" height="2" fill="#fff"/><rect x="2.5" y="3" width="1.5" height="3" fill="#fff"/><rect x="5" y="1.5" width="1.5" height="4.5" fill="#fff"/><path d="M11 5 l3-3 l3 3z" fill="#fff"/><rect x="21" y="1" width="8" height="4" rx="1" fill="#fff"/></svg></div>
  <div class="kebab" style="top:36px"><i></i><i></i><i></i></div>
  <div class="brand" style="top:24px"><span class="dot"></span>RelayCover</div>
  <div class="tabs" style="top:72px;font-size:7.2px">
    <span class="tab on"><svg viewBox="0 0 8 8"><rect x="1" y="0.5" width="6" height="7" rx="1" fill="#4a86c6"/></svg>My Assignments</span>
    <span class="tab"><svg viewBox="0 0 8 8"><circle cx="4" cy="4" r="3.3" fill="none" stroke="#fff"/><path d="M4 2v2h1.5" stroke="#fff" fill="none"/></svg>Available Openings</span>
    <span class="tab"><svg viewBox="0 0 8 8"><rect x=".5" y="2" width="7" height="5" rx="1" fill="#fff"/></svg>My</span>
  </div>
  <div class="list-title" style="top:129px;font-size:11px"><span>My Assignments</span><span class="help">?</span></div>
  <div style="position:absolute;left:0;right:0;top:160px;height:448px;overflow:hidden">
  <div class="cards" style="top:0;font-size:7.2px">
    <div class="card" style="height:72px;margin-bottom:7px"><div class="sf">Subbing For:</div><div class="who"><span class="avatar photo" role="img" aria-label="Portrait photo of teacher"></span><div><div class="nm">Clara Whitfield</div><div class="rl">Teacher</div></div></div><div class="meta"><svg class="edit" viewBox="0 0 8 8"><path d="M1 7 L2 5 L6 1 L7 2 L3 6Z" fill="#4a86c6"/></svg><p><span class="k">Location:</span> PHES</p><p><span class="k">Status:</span><span class="pill teal">Complete</span></p><p><span class="k">Time Slots:</span><br>09/02-09/02 (1h 0m).</p></div></div>
    <div class="card" style="height:72px;margin-bottom:7px"><div class="sf">Subbing For:</div><div class="who"><span class="avatar">T</span><div><div class="nm">Extra duty</div><div class="rl">Teacher</div></div></div><div class="meta"><svg class="edit" viewBox="0 0 8 8"><path d="M1 7 L2 5 L6 1 L7 2 L3 6Z" fill="#4a86c6"/></svg><p><span class="k">Location:</span> PHES</p><p><span class="k">Status:</span><span class="pill teal">Complete</span></p><p><span class="k">Time Slots:</span><br>07/1007/11 (1h 20m)</p></div></div>
    <div class="card" style="height:72px;margin-bottom:7px"><div class="sf">Subbing For:</div><div class="who"><span class="avatar">OH</span><div><div class="nm">Owen Hartley</div><div class="rl">Teacher</div></div></div><div class="meta"><svg class="edit" viewBox="0 0 8 8"><path d="M1 7 L2 5 L6 1 L7 2 L3 6Z" fill="#4a86c6"/></svg><p><span class="k">Location:</span> PHES</p><p><span class="k">Status:</span><span class="pill teal">Complete</span></p><p><span class="k">Time Slots:</span><br>07/1007/11 (1h 20m)</p></div></div>
    <div class="card" style="height:72px;margin-bottom:7px"><div class="sf">Subbing For:</div><div class="who"><span class="avatar photo" role="img" aria-label="Portrait photo of administrator"></span><div><div class="nm">Reid Calloway</div><div class="rl">Administrator</div></div></div><div class="meta"><svg class="edit" viewBox="0 0 8 8"><path d="M1 7 L2 5 L6 1 L7 2 L3 6Z" fill="#4a86c6"/></svg><p><span class="k">Location:</span> PHES</p><p><span class="k">Status:</span><span class="pill green">Active</span></p><p><span class="k">Time Slots:</span><br>07/26-08/07 (14h 15m)</p></div></div>
    <div class="card" style="height:72px;margin-bottom:7px"><div class="sf">Subbing For:</div><div class="who"><span class="avatar photo" role="img" aria-label="Portrait photo of teacher"></span><div><div class="nm">Nadia Ferrante</div><div class="rl">Teacher</div></div></div><div class="meta"><svg class="edit" viewBox="0 0 8 8"><path d="M1 7 L2 5 L6 1 L7 2 L3 6Z" fill="#4a86c6"/></svg><p><span class="k">Location:</span> PHES</p><p><span class="k">Status:</span><span class="pill red">Canceled</span></p><p><span class="k">Time Slots:</span><br>07/31-07/31 (9h 0m)</p></div></div>
    <div class="card" style="height:72px"><div class="sf">Subbing For:</div><div class="who"><span class="avatar photo" role="img" aria-label="Portrait photo of teacher"></span><div><div class="nm">Miles Okafor</div><div class="rl">Teacher</div></div></div><div class="meta"><svg class="edit" viewBox="0 0 8 8"><path d="M1 7 L2 5 L6 1 L7 2 L3 6Z" fill="#4a86c6"/></svg><p><span class="k">Location:</span> PHES</p><p><span class="k">Status:</span><span class="pill green">Active</span></p><p><span class="k">Time Slots:</span></p></div></div>
  </div>
  </div>
  <div class="indicator" style="top:624px"></div>
</section>

</div>
</body>
</html>
```